BrindleStaffing Business Card Design

We are a staffing company finding positions for dedicated nurses and physicians.

Target Market(s)

Business Professionals

Industry/Entity Type

Staffing

Contact Information for Business Card

Gordon Pratley
Chairman
417 39th Avenue South
SAINT PETERSBURG FL 33712
813-555-4172 Mobile
813-555-8036 Fax
gpratley@brindlestaffing.com
www.brindlestaffing.com

Font styles to use
Sans Serif

Colors
fbee3e
f04a50
f37122

Requirements
Must have
• Logo Attached, see colors below. We'd like to see Yellow, Orange and Red.

```html
<!DOCTYPE html>
<html lang="en">
<head>
<meta charset="utf-8">
<title>BrindleStaffing Business Card</title>
<link rel="stylesheet" href="https://fonts.googleapis.com/css2?family=Poppins:wght@700&family=Open+Sans:wght@400;700&display=swap">
<style>
  :root {
    --stage: #1d1d1d;
    --brand-orange: #f37122;
    --brand-red: #f04a50;
    --brand-yellow: #fbee3e;
    --fold-red: #b83238;
    --paper: #ffffff;
    --ink-light: #ffffff;
  }
  html, body {
    margin: 0;
    width: 1200px;
    height: 960px;
    overflow: hidden;
    background: var(--stage);
  }
  .canvas {
    position: relative;
    width: 1200px;
    height: 960px;
  }
  .card {
    position: absolute;
    left: 210px;
    width: 780px;
    height: 446px;
    overflow: hidden;
  }
  .card--front { top: 24px; background: var(--brand-orange); }
  .card--back { top: 490px; background: var(--paper); }

  .wordmark {
    font-family: "Poppins", sans-serif;
    font-weight: 700;
    letter-spacing: -1px;
    margin: 0;
    white-space: nowrap;
  }
  .front-wordmark {
    position: absolute;
    top: 150px;
    width: 100%;
    text-align: center;
    font-size: 70px;
    color: var(--ink-light);
  }
  .front-web {
    position: absolute;
    top: 270px;
    width: 100%;
    text-align: center;
    font-family: "Open Sans", sans-serif;
    font-size: 19px;
    letter-spacing: 3px;
    color: var(--brand-yellow);
    margin: 0;
  }
  .front-web strong { font-weight: 700; }

  .back-shapes { position: absolute; inset: 0; }
  .back-wordmark {
    position: absolute;
    left: 40px;
    top: 126px;
    font-size: 38px;
    color: var(--brand-orange);
  }
  .identity {
    position: absolute;
    right: 36px;
    top: 146px;
    text-align: right;
    font-family: "Open Sans", sans-serif;
    color: var(--ink-light);
  }
  .identity__name { margin: 0; font-size: 25px; font-weight: 700; line-height: 1.2; }
  .identity__title { margin: 0; font-size: 20px; line-height: 1.3; }

  .contact {
    position: absolute;
    right: 36px;
    top: 246px;
    text-align: right;
    font-family: "Open Sans", sans-serif;
    font-size: 18px;
    line-height: 1.4;
    color: var(--ink-light);
    margin: 0;
    font-style: normal;
  }
  .contact__address { margin-bottom: 10px; }
  .contact__line { display: flex; justify-content: flex-end; align-items: center; gap: 10px; }
  .contact__line svg { width: 16px; height: 16px; flex: none; }
</style>
</head>
<body>
<main class="canvas">
  <section class="card card--front" aria-label="Card front">
    <p class="wordmark front-wordmark">BrindleStaffing</p>
    <p class="front-web">www.<strong>brindlestaffing</strong>.com</p>
  </section>

  <section class="card card--back" aria-label="Card back">
    <svg class="back-shapes" viewBox="0 0 780 446" width="780" height="446" aria-hidden="true">
      <polygon points="470,0 780,0 780,446 215,446" fill="var(--brand-orange)"/>
      <polygon points="372,130 402,148 402,232 386,232 372,168" fill="var(--fold-red)"/>
      <polygon points="372,130 780,130 780,232 402,232 402,148" fill="var(--brand-red)"/>
      <rect x="402" y="228" width="378" height="4" fill="var(--brand-yellow)"/>
    </svg>

    <p class="wordmark back-wordmark">BrindleStaffing</p>

    <div class="identity">
      <p class="identity__name">Gordon Pratley</p>
      <p class="identity__title">Chairman</p>
    </div>

    <address class="contact">
      <div class="contact__address">417 39th Avenue South<br>Saint petersburg fl 33712</div>
      <div class="contact__line">813-555-4172 Mobile
        <svg viewBox="0 0 16 16" aria-hidden="true"><circle cx="8" cy="8" r="7" fill="none" stroke="currentColor" stroke-width="1.3"/><path d="M5.6 4.5l1.4 1.6-.8 1a5 5 0 0 0 2.7 2.7l1-.8 1.6 1.4-.9 1.1C8.2 11.3 4.7 7.8 4.5 5.4z" fill="currentColor"/></svg>
      </div>
      <div class="contact__line">813-555-8036 Fax
        <svg viewBox="0 0 16 16" aria-hidden="true"><circle cx="8" cy="8" r="7" fill="none" stroke="currentColor" stroke-width="1.3"/><rect x="5.5" y="4" width="5" height="3" fill="none" stroke="currentColor" stroke-width="1"/><rect x="4" y="7" width="8" height="4.5" fill="currentColor"/></svg>
      </div>
      <div class="contact__line">gpratley@brindlestaffing.com
        <svg viewBox="0 0 16 16" aria-hidden="true"><circle cx="8" cy="8" r="7" fill="none" stroke="currentColor" stroke-width="1.3"/><rect x="4" y="5.5" width="8" height="5.5" fill="none" stroke="currentColor" stroke-width="1.1"/><path d="M4 5.5l4 3 4-3" fill="none" stroke="currentColor" stroke-width="1.1"/></svg>
      </div>
      <div class="contact__line">www.brindlestaffing.com
        <svg viewBox="0 0 16 16" aria-hidden="true"><circle cx="8" cy="8" r="7" fill="none" stroke="currentColor" stroke-width="1.3"/><ellipse cx="8" cy="8" rx="3" ry="7" fill="none" stroke="currentColor" stroke-width="1"/><path d="M1 8h14M2.5 4.5h11M2.5 11.5h11" stroke="currentColor" stroke-width="1"/></svg>
      </div>
    </address>
  </section>
</main>
</body>
</html>
```